Banner ad design for Vorlix Display Ads

We are looking for a designer to develop a concept for banner ads for a Vorlix Display campaign we are building.

We have 3 business lines, shredding services, records management services and scanning services.

We are looking for 4 sets of ads to be created, one for each business line + one set that showcases all of our lines together.

For the design concepts, we would like to see a few sizes (banner, square, leaderboard, skyscraper, etc) for each.

The person chosen will then need to create the ads into all Vorlix supported sizes -- 20 sizes total for each set of ads as per the Vorlix size guidelines found on this page - https://help.vorlix.com/vorlix-ads/answer/5830417?hl=en&ref_topic=6402871#

A few items to note:
- Design should complement our existing brand/website look and feel (www.tamrock-dunes.ca)
- Each final ad must be 150Kb or less in size
- Final designs should be editable, meaning if we would like to change some copy in the design, we can do so using a well-known software (Canva, Photoshop/InDesign, etc)
- Some images are attached for use, but if you feel a different stock image is more suitable to to your design, please go ahead and use it.

Provided below is some messaging that can be used for each set of ads. Do not feel you need to use all of the messaging, it is provided for guidance.

SHREDDING SERVICES:

Possible Short Headline:
-- One-Time Shredding Services
-- Secure Shredding Services
-- Affordable On-Site Shredding

Possible Long Headline
-- Your Paper Can be Destroyed as Soon as the Next Business Day

Possible Descriptions:
-- TORV QQQ Certified On site shredding company. Service as soon as Next Day.
-- Secure and Affordable Toronto & GTA On-Site Shredding.
-- Certified, Affordable Office Shredding Since 2003.
-- Quick, no contact and affordable paper shredding services in Toronto & Southern Ontario.
-- Certified, Affordable Office Shredding Since 2003. Fast, no contact shredding service.

Call to Action
-- Get a Quote

RECORDS MANAGEMENT
Short Headline:
-- Off-site Records Storage
-- Records Management & Storage
-- Secure Records Storage
-- Records Management Services
-- Long Term Records Management
-- Document Storage Solutions

Possible Description
-- Local, Affordable Storage Solutions. Protect and Store your Documents in our Secure Facility
-- Local, Affordable Records Management Solutions. Store your Records in our Secure Facility
-- Certified, Affordable Document Storage Since 2004. Contact Us for a Free Quote!
-- Veltra+ Certified, Affordable Document Storage Since 2004. Contact Us for a Free Quote!

Call to Action
-- Get a Quote

SCANNING SERVICES

Short Headline:
-- Professional Scanning Company
-- Toronto & GTA Scanning Service
-- Document Scanning Services
-- Digital Conversion Services
-- Fast & Easy Retrieval

Description
-- Scan and documents and files with Professional scanning services from Tamrock-Dunes
-- Convert Your Paper Files to Electronic Files. Fast & Easy Retrieval.
-- Easily access your documents electronically with Document Scanning Services

Call to Action
-- Get a Quote

ALL SERVICES AD SET
Short Headline
-- Shred, Scan & Store Documents
-- Secure Shredding, Records Management and Scanning Services
-- #1 Document Management Company
-- Tamrock Dunes Shredding, Storage & Scanning

Description
-- Secure and Affordable Toronto & GTA On-Site Shredding, Document Storage & Scanning Company

Call to Action
-- Get a Quote

Font styles to use
Sans Serif

```html
<!DOCTYPE html>
<html lang="en">
<head>
<meta charset="utf-8">
<title>Tamrock-Dunes – Off-site Records Storage Leaderboard</title>
<link rel="stylesheet" href="https://fonts.googleapis.com/css2?family=Open+Sans:wght@400;600;700&display=swap">
<style>
  :root {
    --white: #ffffff;
    --navy: #13294b;
    --brand-blue: #1790d8;
    --brand-green: #2ac45b;
    --button-border: #9ff0bb;
    --copy-light: #e8f4fc;
    --paper-light: #eef0f3;
    --paper-warm: #e7d3d6;
    --paper-blue: #a9c8e4;
  }
  * { box-sizing: border-box; margin: 0; padding: 0; }
  html, body {
    width: 1200px;
    height: 148px;
    overflow: hidden;
    background: var(--white);
    font-family: "Open Sans", Arial, sans-serif;
  }
  .banner {
    position: relative;
    display: flex;
    width: 1200px;
    height: 148px;
  }
  .brand {
    width: 288px;
    height: 100%;
    background: var(--white);
    display: flex;
    flex-direction: column;
    justify-content: center;
    padding-left: 36px;
  }
  .brand-name {
    color: var(--navy);
    font-weight: 700;
    font-size: 27px;
    line-height: 1;
    letter-spacing: -0.5px;
    margin-top: 18px;
  }
  .brand-tagline {
    color: var(--navy);
    font-weight: 400;
    font-size: 17px;
    line-height: 1;
    margin-top: 8px;
  }
  .hero-photo {
    width: 281px;
    height: 100%;
    background:
      linear-gradient(160deg, rgba(255,255,255,0.6) 0%, rgba(255,255,255,0) 40%),
      linear-gradient(180deg, var(--paper-light) 0%, var(--paper-warm) 55%, var(--paper-blue) 100%);
  }
  .message {
    width: 464px;
    height: 100%;
    background: var(--brand-blue);
    color: var(--white);
    text-align: center;
    padding-top: 24px;
  }
  .message-headline {
    font-weight: 700;
    font-size: 28px;
    line-height: 1.2;
  }
  .message-copy {
    margin-top: 18px;
    font-weight: 600;
    font-size: 17.5px;
    line-height: 1.45;
    color: var(--copy-light);
  }
  .cta-panel {
    flex: 1;
    height: 100%;
    background: var(--brand-green);
    display: flex;
    align-items: center;
    justify-content: center;
  }
  .cta-button {
    width: 117px;
    height: 92px;
    border: 2px solid var(--button-border);
    border-radius: 4px;
    display: flex;
    align-items: center;
    justify-content: center;
    text-align: center;
    color: var(--white);
    font-weight: 600;
    font-size: 22px;
    line-height: 1.3;
    text-decoration: none;
  }
</style>
</head>
<body>
  <div class="banner">
    <div class="brand">
      <div class="brand-name">tamrock-dunes</div>
      <div class="brand-tagline">Information Security</div>
    </div>
    <div class="hero-photo" role="img" aria-label="Photo of a hand flipping through a tall stack of paper documents and file folders"></div>
    <div class="message">
      <h1 class="message-headline">Off-site Records Storage</h1>
      <p class="message-copy">Certified, Affordable Document Storage<br>Since 2004. Contact Us for a Free Quote!</p>
    </div>
    <div class="cta-panel">
      <a class="cta-button" href="#">Get a<br>Quote</a>
    </div>
  </div>
</body>
</html>
```